Larkfield Ridge Management

I need a professional website. My current website is larkfieldridgemanagement.com and I hate it. It was created with some AI tool very quickly because I needed a site up and running with no advanced notice. I’m open to all designs .. I trust you, the professionals will deliver the results I’m anxiously awaiting! :)

```html
<!DOCTYPE html>
<html lang="en">
<head>
<meta charset="UTF-8">
<title>Larkfield Ridge Management — Partnership Tiers</title>
<link href="https://fonts.googleapis.com/css2?family=Montserrat:wght@700;800;900&family=Inter:wght@400;500;600;700&display=swap" rel="stylesheet">
<style>
:root{
  --navy:#1f2c46;
  --red:#c1272d;
  --paper:#f6f7f9;
  --white:#ffffff;
  --ink:#3b4354;
  --muted:#7c8599;
  --rule:#6a6d74;
}
*{box-sizing:border-box;margin:0;padding:0}
html,body{width:1200px;height:1051px;overflow:hidden}
body{background:var(--paper);font-family:"Inter",sans-serif;color:var(--ink);position:relative}

.site-header{position:absolute;left:0;top:0;width:1200px;height:70px;background:var(--white)}
.nav-link{position:absolute;top:30px;font-size:9.5px;font-weight:600;letter-spacing:1.3px;color:var(--navy);text-transform:uppercase}
.brand{position:absolute;left:540px;top:22px;width:120px;text-align:center;font-family:"Montserrat",sans-serif;font-weight:800;font-size:12px;line-height:13px;color:var(--navy);text-transform:uppercase}
.brand-mark{display:inline-block;width:8px;height:8px;background:var(--red);margin-right:4px;vertical-align:1px}
.btn-proposal{position:absolute;left:738px;top:18px;width:146px;height:34px;background:var(--red);color:var(--white);font-size:9.5px;font-weight:700;letter-spacing:1.2px;display:flex;align-items:center;justify-content:center;box-shadow:3px 3px 0 var(--navy)}

.hero{position:absolute;left:0;top:90px;width:1200px;height:237px;background:var(--navy);text-align:center}
.eyebrow{position:absolute;top:61px;left:0;width:100%;display:flex;justify-content:center;align-items:center;gap:10px;color:var(--white);font-family:"Montserrat",sans-serif;font-weight:800;font-size:9px;letter-spacing:2.2px}
.eyebrow::before,.eyebrow::after{content:"";width:30px;height:2px;background:var(--red)}
.hero h1{position:absolute;top:86px;left:0;width:100%;font-family:"Montserrat",sans-serif;font-weight:900;font-size:38.5px;letter-spacing:-1px;color:var(--white)}
.hero p{position:absolute;top:140px;left:340px;width:520px;font-size:11.8px;line-height:18.3px;color:#e3e6ee}

.tiers{position:absolute;top:387px;left:220px;display:flex;gap:21px}
.tier{position:relative;width:239px;height:513px;background:var(--white);border:1.5px solid var(--navy);box-shadow:3px 3px 0 var(--navy);padding:26px 25px 0 25px}
.badge{position:absolute;top:-1px;right:-1px;width:106px;height:21px;background:var(--red);color:var(--white);font-family:"Montserrat",sans-serif;font-weight:800;font-size:6.5px;letter-spacing:1.2px;display:flex;align-items:center;justify-content:center}
.tier h2{font-family:"Montserrat",sans-serif;font-weight:900;font-size:15.5px;line-height:18.7px;color:var(--navy);text-transform:uppercase;letter-spacing:-.3px;width:180px}
.tier .lede{margin-top:13px;font-size:10.5px;line-height:16.3px;color:var(--ink)}
.tier hr{border:0;border-top:1.5px solid var(--navy);margin:21px 0 22px}
.features{list-style:none}
.features li{position:relative;padding-left:23px;font-size:10.5px;line-height:16.3px;font-weight:500;color:var(--ink);margin-bottom:13px}
.features li svg{position:absolute;left:0;top:1px;width:12px;height:12px}
.tier .cta{position:absolute;left:25px;bottom:26px;width:187px;height:34px;display:flex;align-items:center;justify-content:center;font-family:"Montserrat",sans-serif;font-weight:800;font-size:9px;letter-spacing:1.2px;border:1.5px solid var(--navy);box-shadow:2px 2px 0 var(--navy);color:var(--navy);background:var(--white)}
.tier .cta.primary{background:var(--red);color:var(--white)}

.site-footer{position:absolute;left:0;top:960px;width:1200px;height:91px;background:var(--navy);border-top:4px solid var(--rule)}
.footer-brand{position:absolute;left:205px;top:30px;width:56px;text-align:center;font-family:"Montserrat",sans-serif;font-weight:800;font-size:7.5px;line-height:9px;color:var(--white);text-transform:uppercase}
.footer-divider{position:absolute;left:264px;top:38px;width:1px;height:16px;background:#3a4661}
.footer-text{position:absolute;top:38px;font-size:7.5px;line-height:10px;font-weight:600;letter-spacing:1.1px;text-transform:uppercase}
.copy{left:284px;color:#b9c0cf}
.region{left:443px;color:var(--muted);width:230px}
.flink{color:#b9c0cf}
.flink.strong{color:var(--white);font-weight:700}
</style>
</head>
<body>
<header class="site-header">
  <span class="nav-link" style="left:386px">Services</span>
  <span class="nav-link" style="left:461px">Why Larkfield</span>
  <div class="brand"><span class="brand-mark"></span>Larkfield<br>Ridge</div>
  <span class="nav-link" style="left:663px">Contact</span>
  <a class="btn-proposal">REQUEST PROPOSAL</a>
</header>

<section class="hero">
  <div class="eyebrow">PARTNERSHIP TIERS</div>
  <h1>TAILORED MANAGEMENT SOLUTIONS</h1>
  <p>Explore our comprehensive property management packages and specialized consulting services. Select the level of partnership that fits your portfolio's needs.</p>
</section>

<main class="tiers">
  <article class="tier">
    <div class="badge">PREMIUM CHOICE</div>
    <h2>Comprehensive Asset Management</h2>
    <p class="lede">The ultimate "hands-off" solution for out-of-state investors and high-net-worth owners. We handle every aspect of your property's lifecycle.</p>
    <hr>
    <ul class="features">
      <li><svg viewBox="0 0 12 12"><rect width="12" height="12" rx="2" fill="#1f2c46"/><path d="M3.3 6.2l1.8 1.8 3.6-3.8" stroke="#fff" stroke-width="1.4" fill="none"/></svg>Aggressive multi-channel marketing &amp; tenant placement</li>
      <li><svg viewBox="0 0 12 12"><rect width="12" height="12" rx="2" fill="#1f2c46"/><path d="M3.3 6.2l1.8 1.8 3.6-3.8" stroke="#fff" stroke-width="1.4" fill="none"/></svg>Stringent background, credit, and financial screening</li>
      <li><svg viewBox="0 0 12 12"><rect width="12" height="12" rx="2" fill="#1f2c46"/><path d="M3.3 6.2l1.8 1.8 3.6-3.8" stroke="#fff" stroke-width="1.4" fill="none"/></svg>24/7 proactive and emergency maintenance dispatch</li>
      <li><svg viewBox="0 0 12 12"><rect width="12" height="12" rx="2" fill="#1f2c46"/><path d="M3.3 6.2l1.8 1.8 3.6-3.8" stroke="#fff" stroke-width="1.4" fill="none"/></svg>Rent collection, lease enforcement, and eviction management</li>
      <li><svg viewBox="0 0 12 12"><rect width="12" height="12" rx="2" fill="#1f2c46"/><path d="M3.3 6.2l1.8 1.8 3.6-3.8" stroke="#fff" stroke-width="1.4" fill="none"/></svg>Data-driven monthly financial reporting via Owner Portal</li>
    </ul>
    <a class="cta primary">INQUIRE ABOUT MANAGEMENT</a>
  </article>

  <article class="tier">
    <h2>Premium Tenant Placement</h2>
    <p class="lede">For the hands-on owner who wants to manage their own property but needs the security of a rigorously vetted tenant.</p>
    <hr>
    <ul class="features">
      <li><svg viewBox="0 0 12 12"><rect width="12" height="12" rx="2" fill="#1f2c46"/><path d="M3.3 6.2l1.8 1.8 3.6-3.8" stroke="#fff" stroke-width="1.4" fill="none"/></svg>Professional real estate photography and listing optimization</li>
      <li><svg viewBox="0 0 12 12"><rect width="12" height="12" rx="2" fill="#1f2c46"/><path d="M3.3 6.2l1.8 1.8 3.6-3.8" stroke="#fff" stroke-width="1.4" fill="none"/></svg>Property showings and lead management</li>
      <li><svg viewBox="0 0 12 12"><rect width="12" height="12" rx="2" fill="#1f2c46"/><path d="M3.3 6.2l1.8 1.8 3.6-3.8" stroke="#fff" stroke-width="1.4" fill="none"/></svg>Complete background and financial screening framework</li>
      <li><svg viewBox="0 0 12 12"><rect width="12" height="12" rx="2" fill="#1f2c46"/><path d="M3.3 6.2l1.8 1.8 3.6-3.8" stroke="#fff" stroke-width="1.4" fill="none"/></svg>Custom, legally compliant lease drafting and execution</li>
      <li><svg viewBox="0 0 12 12"><rect width="12" height="12" rx="2" fill="#1f2c46"/><path d="M3.3 6.2l1.8 1.8 3.6-3.8" stroke="#fff" stroke-width="1.4" fill="none"/></svg>Seamless move-in coordination and first month's rent collection</li>
    </ul>
    <a class="cta">SECURE A TENANT</a>
  </article>

  <article class="tier">
    <h2>Real Estate Advisory Services</h2>
    <p class="lede">Strategic guidance for investors looking to acquire, stabilize, or scale their rental portfolios in the Northeast Ohio market.</p>
    <hr>
    <ul class="features">
      <li><svg viewBox="0 0 12 12"><rect width="12" height="12" rx="2" fill="#1f2c46"/><path d="M3.3 6.2l1.8 1.8 3.6-3.8" stroke="#fff" stroke-width="1.4" fill="none"/></svg>Cleveland/Akron market analysis and rent projections</li>
      <li><svg viewBox="0 0 12 12"><rect width="12" height="12" rx="2" fill="#1f2c46"/><path d="M3.3 6.2l1.8 1.8 3.6-3.8" stroke="#fff" stroke-width="1.4" fill="none"/></svg>Property acquisition due diligence</li>
      <li><svg viewBox="0 0 12 12"><rect width="12" height="12" rx="2" fill="#1f2c46"/><path d="M3.3 6.2l1.8 1.8 3.6-3.8" stroke="#fff" stroke-width="1.4" fill="none"/></svg>Value-add renovation consulting for maximum ROI</li>
    </ul>
    <a class="cta">SCHEDULE A CONSULTATION</a>
  </article>
</main>

<footer class="site-footer">
  <div class="footer-brand">Larkfield<br>Ridge</div>
  <div class="footer-divider"></div>
  <div class="footer-text copy">© 2026. All rights<br>reserved.</div>
  <div class="footer-text region">Proudly serving Greater Cleveland &amp; Akron, Ohio</div>
  <a class="footer-text flink" style="left:711px">Privacy</a>
  <a class="footer-text flink" style="left:769px">Terms</a>
  <a class="footer-text flink strong" style="left:819px">Owner<br>Portal</a>
  <a class="footer-text flink strong" style="left:907px">Tenant<br>Portal</a>
</footer>
</body>
</html>
```